Harlow Mechanical Contractors needs a Website

Create basic website for commercial plumbing and mechanical contractor; to include pictures of works in progress and completed works, description of all services offered and geographical locations and licenses

Target Market(s)

General Contractors, Real Estate Developers, Construction Companies

Industry/Entity Type

Construction

Coding

Coded - Design and coding required

Number of Pages Required

5+ page

• See logo attached to project

Colors
0392cd

```html
<!DOCTYPE html>
<html lang="en">
<head>
<meta charset="utf-8">
<title>Harlow Mechanical Contractors</title>
<link rel="stylesheet" href="https://fonts.googleapis.com/css2?family=Open+Sans:ital,wght@0,400;0,600;0,700;0,800;1,400&display=swap">
<style>
:root{
  --blue:#0392cd;
  --blue-dark:#0278ab;
  --ink:#333;
  --muted:#777;
  --light:#f1f1f1;
  --line:#d9d9d9;
  --btn:#3d3d3d;
  --footer:#2b2b2b;
  --footer-text:#bdbdbd;
  --white:#fff;
}
*{box-sizing:border-box;margin:0;padding:0}
html,body{width:1200px;height:2476px;overflow:hidden}
body{position:relative;font-family:"Open Sans",Arial,sans-serif;color:var(--ink);background:var(--white)}
.abs{position:absolute}

/* header */
.brand{left:74px;top:20px;display:flex;align-items:center;gap:10px}
.brand-mark{width:58px;height:58px;border-radius:50%;background:var(--blue)}
.brand-name{font-size:14px;font-weight:800;line-height:15px;color:#1d4f7a;text-transform:uppercase;width:120px}
.call{left:566px;top:34px;display:flex;align-items:center;gap:12px}
.call-icon{width:38px;height:38px}
.call small{display:block;font-size:16px;font-weight:700;color:var(--blue);line-height:18px}
.call strong{display:block;font-size:24px;font-weight:700;color:#1d4f7a;line-height:28px}
.search{left:837px;top:37px;width:291px;height:42px;border:1px solid var(--line);background:#f4f4f4;display:flex;align-items:center;justify-content:space-between;padding:0 14px;font-size:12px;color:#888}

/* nav */
.nav{left:0;top:116px;width:1200px;height:47px;background:var(--blue)}
.nav a{position:absolute;top:0;line-height:47px;font-size:13px;font-weight:700;color:var(--white);text-decoration:none;text-transform:uppercase}

/* hero */
.hero{left:0;top:163px;width:1200px;height:494px;background:linear-gradient(90deg,#2c3a45 0%,#4d6272 45%,#6c7f86 70%,#8b9a7a 100%)}
.hero-title{left:74px;top:292px;font-size:45px;font-weight:800;line-height:51px;color:var(--white);text-transform:uppercase}
.hero-sub{left:74px;top:396px;font-size:26px;line-height:37px;color:var(--white);font-weight:600}
.dots{left:74px;top:564px;display:flex;gap:4px}
.dots span{width:16px;height:16px;border-radius:50%;background:var(--white)}
.dots span.on{background:var(--blue)}

/* section headings */
.heading{display:flex;align-items:center;gap:12px;font-size:20px;font-weight:700;color:var(--blue);text-transform:uppercase}
.heading i{width:30px;height:30px;border-radius:50%;background:#1d4f7a;display:block}
.heading.sm{font-size:18px}
.text{font-size:15px;line-height:25px;color:var(--muted)}
.btn{display:inline-block;background:linear-gradient(#4a4a4a,#2f2f2f);color:var(--white);font-size:12px;font-weight:700;text-transform:uppercase;text-align:center;line-height:40px;height:40px;width:132px}
.photo{display:block}

/* quick contact */
.qc{left:794px;top:695px;width:332px;height:444px;background:var(--light)}
.qc-head{height:48px;background:var(--blue);color:var(--white);font-size:21px;font-weight:600;line-height:48px;padding-left:17px;text-transform:uppercase}
.field{position:absolute;left:20px;width:292px;height:38px;background:var(--white);border:1px solid var(--line);font-size:12px;color:#666;padding:0 12px;line-height:36px}
.field.area{height:111px;line-height:22px;padding-top:6px}
.submit{left:182px;top:381px;width:130px;position:absolute}

.testi{left:794px;top:1152px;width:332px;height:210px;background:var(--light);padding:24px 20px}
.testi .heading{font-size:18px;justify-content:space-between}
.testi q{display:block;margin-top:14px;font-size:14px;font-style:italic;line-height:24px;color:var(--muted)}
.testi b{display:block;margin-top:8px;font-size:13px;color:var(--blue)}

/* services band */
.band{left:0;top:1408px;width:1200px;height:405px;background:var(--blue);color:var(--white)}
.band .heading{color:var(--white);justify-content:center;position:absolute;left:0;top:50px;width:1200px}
.band .heading i{background:var(--white)}
.svc{position:absolute;top:120px;width:330px;text-align:center}
.svc-icon{width:100px;height:100px;border:3px solid var(--white);border-radius:50%;margin:0 auto;display:flex;align-items:center;justify-content:center}
.svc h3{margin-top:22px;font-size:17px;font-weight:700;text-transform:uppercase}
.svc p{margin-top:14px;font-size:15px;line-height:25px}

/* projects */
.proj{position:absolute;top:1922px;width:210px}
.proj .photo{height:143px}
.proj h4{margin-top:18px;font-size:17px;font-weight:700;color:var(--blue)}
.proj p{margin-top:2px;font-size:15px;line-height:25px;color:var(--muted)}

.blog{left:794px;top:1859px;width:332px;height:297px;background:var(--light);padding:20px 20px}
.post{margin-top:18px}
.post h5{font-size:16px;font-weight:700;color:var(--blue)}
.post p{font-size:15px;line-height:24px;color:var(--muted);margin-top:2px}
.post em{font-style:normal;font-size:13px;font-weight:700;color:var(--blue)}

/* footer */
.footer{left:0;top:2193px;width:1200px;height:283px;background:var(--footer);color:var(--footer-text);font-size:13px}
.footer .brand{left:74px;top:38px}
.footer .brand-name{color:var(--white)}
.copy{left:76px;top:138px;line-height:24px}
.social{left:76px;top:214px;display:flex;gap:9px}
.social span{width:30px;height:30px;border-radius:50%;background:#5a5a5a}
.fcol h6{font-size:15px;font-weight:700;color:var(--blue);text-transform:uppercase;margin-bottom:10px}
.fcol a{display:block;color:var(--footer-text);text-decoration:none;line-height:33px}
.contact-line{display:flex;align-items:center;gap:10px;line-height:24px}
</style>
</head>
<body>

<header>
  <div class="abs brand"><span class="brand-mark"></span><span class="brand-name">Harlow Mechanical Contractors</span></div>
  <div class="abs call">
    <svg class="call-icon" viewBox="0 0 38 38"><circle cx="19" cy="19" r="17" fill="none" stroke="#0392cd" stroke-width="2"/><path d="M13 11c1-1 2-1 3 0l2 3c.5 1 .3 2-.5 2.6l-1 .8c1 2.3 2.8 4.1 5.1 5.1l.8-1c.6-.8 1.6-1 2.6-.5l3 2c1 1 1 2 0 3l-1.4 1.4C24 29 12 18 11.6 12.4z" fill="#0392cd"/></svg>
    <div><small>CALL US:</small><strong>1-800-555-0142</strong></div>
  </div>
  <div class="abs search">Search..
    <svg width="18" height="18" viewBox="0 0 18 18"><circle cx="7.5" cy="7.5" r="5.5" fill="none" stroke="#0392cd" stroke-width="2.4"/><path d="M11.5 11.5l5 5" stroke="#0392cd" stroke-width="2.6" stroke-linecap="round"/></svg>
  </div>
</header>

<nav class="abs nav">
  <a style="left:76px">Home</a>
  <a style="left:167px">About Us</a>
  <a style="left:287px">Our Services</a>
  <a style="left:433px">Clients</a>
  <a style="left:538px">Blog</a>
  <a style="left:627px">Latest News</a>
  <a style="left:766px">Testimonials</a>
  <a style="left:918px">Careers</a>
  <a style="left:1027px">Contact Us</a>
</nav>

<section class="abs hero" role="img" aria-label="Engineer in a hard hat inspecting large industrial pipework"></section>
<h1 class="abs hero-title">Commercial Plumbing<br>and Mechanical Contractor</h1>
<p class="abs hero-sub">We install full plumbing services for large offices, condominiums,<br>and industrial projects.</p>
<div class="abs dots"><span class="on"></span><span></span><span></span><span></span></div>

<section class="abs" style="left:74px;top:698px;width:691px">
  <h2 class="heading"><i></i>Welcome to Our Website</h2>
  <p class="text" style="margin-top:16px">Aliquam molestie, mi et imperdiet euismod, dui purus auctor tellus, et interdum lacus lectus et ante. Sed accumsan sollicitudin sapien, sit amet adipiscing turpis gravida ac. In congue, neque ac lobortis volutpat, libero mauris varius mi, vitae suscipit ipsum ligula vitae risus. Duis aliquam nibh a dui iaculis viverra id a velit. Vivamus egestas risus in magna varius commodo.</p>
  <span class="btn" style="margin-top:26px">Read More</span>
</section>
<div class="abs" style="left:74px;top:941px;width:691px;height:1px;background:var(--line)"></div>

<section class="abs" style="left:74px;top:968px;width:331px">
  <h2 class="heading sm"><i></i>Commercial Plumbing</h2>
  <div class="photo" role="img" aria-label="Plumber fitting a red pipe valve" style="margin-top:13px;height:183px;background:linear-gradient(135deg,#5c6b7a,#2e3a4d 60%,#9a3a3a)"></div>
  <p class="text" style="margin-top:16px">Aliquam molestie, mi et imperdiet euismod, dui purus auctor tellus, et interdum lacus lectus et ante.</p>
  <span class="btn" style="margin-top:26px">Read More</span>
</section>
<section class="abs" style="left:434px;top:968px;width:331px">
  <h2 class="heading sm"><i></i>Mechanical Contractor</h2>
  <div class="photo" role="img" aria-label="Two technicians working on mechanical equipment" style="margin-top:13px;height:183px;background:linear-gradient(135deg,#9aa7ae,#3f5c8c 55%,#6f7f88)"></div>
  <p class="text" style="margin-top:16px">Aliquam molestie, mi et imperdiet euismod, dui purus auctor tellus, et interdum lacus lectus et ante.</p>
  <span class="btn" style="margin-top:26px">Read More</span>
</section>

<aside class="abs qc">
  <div class="qc-head">Quick Contact</div>
  <div class="field" style="top:66px">Enter Name</div>
  <div class="field" style="top:114px">Enter Email Address</div>
  <div class="field" style="top:160px">Phone Number</div>
  <div class="field" style="top:208px;display:flex;justify-content:space-between;align-items:center">Select Services
    <svg width="10" height="6" viewBox="0 0 10 6"><path d="M1 1l4 4 4-4" fill="none" stroke="#666" stroke-width="1.5"/></svg></div>
  <div class="field area" style="top:256px">Message</div>
  <span class="btn submit">Submit Now</span>
</aside>

<aside class="abs testi">
  <h2 class="heading"><span>Testimonials</span>
    <svg width="28" height="14" viewBox="0 0 28 14"><path d="M7 2L2 7l5 5M21 2l5 5-5 5" fill="none" stroke="#0392cd" stroke-width="2"/></svg></h2>
  <q>“ Suspendisse lobortis turpis in odio blandit ac interdum lorem euismodetiam risus massa, vulputate eu pellentesque et, consectetur a neque....”</q>
  <b>-Name Heading</b>
</aside>

<section class="abs band">
  <h2 class="heading"><i></i>Our Services Offers</h2>
  <div class="svc" style="left:76px">
    <div class="svc-icon"><svg width="46" height="46" viewBox="0 0 46 46" fill="#fff"><rect x="10" y="6" width="20" height="36"/><rect x="30" y="18" width="8" height="24"/><g fill="#0392cd"><rect x="13" y="10" width="4" height="4"/><rect x="20" y="10" width="4" height="4"/><rect x="13" y="17" width="4" height="4"/><rect x="20" y="17" width="4" height="4"/><rect x="13" y="24" width="4" height="4"/><rect x="20" y="24" width="4" height="4"/><rect x="13" y="31" width="4" height="4"/><rect x="20" y="31" width="4" height="4"/><rect x="32" y="22" width="4" height="3"/><rect x="32" y="28" width="4" height="3"/></g></svg></div>
    <h3>Large Offices</h3>
    <p>Aliquam molestie, mi et imperdiet euismod, dui purus auctor tellus, et interdum lacus lectus et ante.</p>
  </div>
  <div class="svc" style="left:434px">
    <div class="svc-icon"><svg width="50" height="46" viewBox="0 0 50 46" fill="#fff"><path d="M25 4L3 20h6v22h32V20h6z"/><g fill="#0392cd"><rect x="14" y="22" width="6" height="6"/><rect x="30" y="22" width="6" height="6"/><rect x="14" y="32" width="6" height="6"/><rect x="22" y="30" width="6" height="12"/><rect x="30" y="32" width="6" height="6"/></g></svg></div>
    <h3>Condominiums</h3>
    <p>Aliquam molestie, mi et imperdiet euismod, dui purus auctor tellus, et interdum lacus lectus et ante.</p>
  </div>
  <div class="svc" style="left:796px">
    <div class="svc-icon"><svg width="52" height="46" viewBox="0 0 52 46" fill="#fff"><path d="M4 42V22l12 8v-8l12 8v-8l12 8V6h7v36z"/><circle cx="43" cy="4" r="3"/><g fill="#0392cd"><rect x="9" y="34" width="5" height="4"/><rect x="19" y="34" width="5" height="4"/><rect x="29" y="34" width="5" height="4"/></g></svg></div>
    <h3>Industrial Projects</h3>
    <p>Aliquam molestie, mi et imperdiet euismod, dui purus auctor tellus, et interdum lacus lectus et ante.</p>
  </div>
</section>

<h2 class="abs heading" style="left:74px;top:1862px"><i></i>Recent Projects</h2>
<article class="proj" style="left:74px">
  <div class="photo" role="img" aria-label="Workers in hard hats and hi-vis vests on an industrial site" style="background:linear-gradient(135deg,#b9c7d4,#6b7a4a 60%,#c8d23a)"></div>
  <h4>Aliquam molestie</h4><p>Vestibulum ante ipsum primis in faucibus..</p>
</article>
<article class="proj" style="left:317px">
  <div class="photo" role="img" aria-label="Engineers reviewing plans beside large pipes" style="background:linear-gradient(135deg,#3b5c86,#2c3b52 55%,#b9c23e)"></div>
  <h4>Aliquam molestie</h4><p>Vestibulum ante ipsum primis in faucibus..</p>
</article>
<article class="proj" style="left:558px">
  <div class="photo" role="img" aria-label="Technician inspecting a plant room with pipework" style="background:linear-gradient(135deg,#c9ccd0,#6d7784 55%,#9aa2aa)"></div>
  <h4>Aliquam molestie</h4><p>Vestibulum ante ipsum primis in faucibus..</p>
</article>

<aside class="abs blog">
  <h2 class="heading"><i></i>Blog Posts</h2>
  <div class="post"><h5>Aliquam molestie porttitor nec..</h5><p>Vestibulum ante ipsum primis egestas risus in magna...</p><em>Posted on 2hrs ago</em></div>
  <div class="post"><h5>Aliquam molestie porttitor nec..</h5><p>Vestibulum ante ipsum primis egestas risus in magna...</p><em>Posted on 2hrs ago</em></div>
</aside>

<footer class="abs footer">
  <div class="abs brand" style="top:36px;left:76px"><span class="brand-mark"></span><span class="brand-name">Harlow Mechanical Contractors</span></div>
  <p class="abs copy">Copyright © 2016. Company Name.<br>All Right Reserved</p>
  <div class="abs social"><span></span><span></span><span></span><span></span><span></span></div>

  <div class="abs fcol" style="left:355px;top:34px"><h6>Site Map</h6>
    <a>Home</a><a>About Us</a><a>Our Services</a><a>Clients</a><a>Blog</a></div>
  <div class="abs fcol" style="left:488px;top:34px"><h6>&nbsp;</h6>
    <a>Latest News</a><a>Testimonials</a><a>Careers</a><a>Contact Us</a></div>
  <div class="abs fcol" style="left:666px;top:34px"><h6>Services</h6>
    <a>Duis aliquam nibh</a><a>Dui iaculis viverra</a><a>Vivamus egestas</a><a>Risus in magna</a></div>
  <div class="abs fcol" style="left:885px;top:34px;width:240px"><h6>Contact Us</h6>
    <p style="font-weight:700;color:#ddd;line-height:24px">HARLOW MECHANICAL CONTRACTOR</p>
    <p style="line-height:22px">4120 Elmstead Road,<br>Glasgow, G12 8QT</p>
    <p class="contact-line" style="margin-top:6px"><svg width="12" height="12" viewBox="0 0 12 12"><path d="M2 1c.5-.5 1-.5 1.5 0l1.5 2c.3.5.2 1-.2 1.3l-.6.5a5 5 0 0 0 3 3l.5-.6c.3-.4.8-.5 1.3-.2l2 1.5c.5.5.5 1 0 1.5l-.8.8C6 11 1 6 1.2 1.8z" fill="#fff"/></svg>1-800-555-0142</p>
    <p class="contact-line"><svg width="12" height="10" viewBox="0 0 12 10"><rect x="0" y="0" width="12" height="10" fill="#fff"/><path d="M0 0l6 5 6-5" fill="none" stroke="#2b2b2b" stroke-width="1.2"/></svg>info@harlowmechanical.com</p>
  </div>
</footer>

</body>
</html>
```